Telecommunications/Power civil contractor needs business card design

Were a new telecommunications/power underground civil contractor that is looking for a new business card design. Our company colours are silver or grey and orange. Feel free to use the white background logo or the black background logo.

Target Market(s)

Local contractors, utility companies, private sector mining/energy companies, developers.

Industry/Entity Type

Telecommunications

Contact Information for Business Card

Each card will need the following info:
Persons name:
Title:
E-mail:
Phone number:
Shop Address:
Mailing Address:

Requirements
Must have
• Each card will need the following info:
• Persons name:
• Title:
• E-mail:
• Phone number:
• Shop Address:
• Mailing Address:

```html
<!DOCTYPE html>
<html lang="en">
<head>
<meta charset="utf-8">
<title>Ridgeline Trench Works Inc — Business Card</title>
<link rel="stylesheet" href="https://fonts.googleapis.com/css2?family=Open+Sans:wght@400;700;800&display=swap">
<style>
  :root {
    --bg: #2b2b2d;
    --orange: #f15a24;
    --white: #ffffff;
    --grey: #8a8a8c;
    --grey-dark: #5d5d60;
    --grey-light: #c9c9cb;
    --black: #141414;
    --black-soft: #1f1f20;
  }
  * { box-sizing: border-box; margin: 0; padding: 0; }
  html, body {
    width: 1200px; height: 925px; overflow: hidden;
    background: var(--bg);
    font-family: "Open Sans", Arial, sans-serif;
  }
  .stage {
    position: relative; width: 1200px; height: 925px;
    display: flex; align-items: center; justify-content: center; gap: 50px;
  }
  .card {
    position: relative; width: 540px; height: 310px; overflow: hidden;
    box-shadow: 0 14px 30px rgba(0,0,0,.45);
  }
  .card-front { background: var(--white); }
  .front-shapes { position: absolute; inset: 0; }

  .brand {
    position: absolute; display: flex; align-items: center; gap: 14px;
  }
  .brand-mark {
    width: 58px; height: 58px; border-radius: 50%;
    border: 5px solid var(--grey); flex: none;
  }
  .brand-name {
    color: var(--orange); font-weight: 800; text-transform: uppercase;
    line-height: 1.05; letter-spacing: .5px;
  }
  .brand-name .line-main { display: block; font-size: 26px; }
  .brand-name .line-sub { display: block; font-size: 12.5px; letter-spacing: 1.6px; }

  .card-front .brand { left: 30px; top: 118px; }

  .contact {
    position: absolute; right: 26px; top: 26px;
    color: var(--white); text-align: right; font-size: 12.5px; line-height: 1.5;
  }
  .contact .person-name { font-weight: 700; font-size: 14px; }
  .contact .person-title { margin-bottom: 14px; }
  .contact .address { margin-bottom: 12px; }
  .contact .row { display: flex; justify-content: flex-end; align-items: center; gap: 7px; }
  .contact .icon { width: 12px; height: 12px; flex: none; }

  .card-back {
    background: linear-gradient(135deg, var(--black-soft), var(--black));
  }
  .card-back .brand {
    left: 50%; top: 50%; transform: translate(-50%, -50%);
  }
</style>
</head>
<body>
<main class="stage">

  <section class="card card-front" aria-label="Business card front">
    <svg class="front-shapes" viewBox="0 0 540 310" width="540" height="310" aria-hidden="true">
      <defs>
        <linearGradient id="swoosh" x1="0" y1="0" x2="1" y2="0">
          <stop offset="0" stop-color="#eeeeee"/>
          <stop offset=".5" stop-color="#8a8a8c"/>
          <stop offset="1" stop-color="#4a4a4c"/>
        </linearGradient>
      </defs>
      <path d="M215,0 C300,30 250,270 330,310 L540,310 L540,0 Z" fill="url(#swoosh)"/>
      <path d="M245,0 C320,30 275,270 350,310 L540,310 L540,0 Z" fill="var(--orange)"/>
    </svg>

    <div class="brand">
      <span class="brand-mark"></span>
      <span class="brand-name">
        <span class="line-main">Ridgeline</span>
        <span class="line-sub">Trench Works Inc</span>
      </span>
    </div>

    <div class="contact">
      <p class="person-name">Marlow Teague</p>
      <p class="person-title">Managing Director</p>
      <p class="address">48 Cedar Loop,<br>Suite 210, Yakima, WA 98901</p>
      <p class="row">509.555.0142
        <svg class="icon" viewBox="0 0 12 12" aria-hidden="true"><path d="M2.5 1 L4.5 1 L5.2 3.5 L4 4.5 C4.6 6 6 7.4 7.5 8 L8.5 6.8 L11 7.5 L11 9.5 C11 10.3 10.3 11 9.5 11 C5 11 1 7 1 2.5 C1 1.7 1.7 1 2.5 1 Z" fill="#fff"/></svg>
      </p>
      <p class="row">office@ridgelinetrench.com
        <svg class="icon" viewBox="0 0 12 12" aria-hidden="true"><rect x="1" y="2.5" width="10" height="7" fill="#fff"/><path d="M1 2.5 L6 6.5 L11 2.5" fill="none" stroke="var(--orange)" stroke-width="1"/></svg>
      </p>
    </div>
  </section>

  <section class="card card-back" aria-label="Business card back">
    <div class="brand">
      <span class="brand-mark"></span>
      <span class="brand-name">
        <span class="line-main">Ridgeline</span>
        <span class="line-sub">Trench Works Inc</span>
      </span>
    </div>
  </section>

</main>
</body>
</html>
```